Website to design and sell sundials: www.gnomonvale.com

We have a website that creates a free paper sundial, we want to migrate from this not profit free website to a website where we will continue offering the free paper sundial model but We will also offer a manufactured sundial and sell it.
In order to understand the project, please visit:
http://www.gnomonvale.com/vertical/sundial.html and
http://www.torvel.net/landing/

The website user journey should be redesigned, including the phases that are,
select language
Show product give info
Creation/edit sundial (could be one or more phases)
View created sundial
Buy sundial.

May some of them could be combined or splitted, what It have more sense.

Requirements
Must have
• A description page user journey offering freemium paper sundial and physical sundial to sell.
• A sundial creation page for "free" paper sundial
• A result page for paper sundial
• A sell page for physical

```html
<!DOCTYPE html>
<html lang="en">
<head>
<meta charset="utf-8">
<title>GnomonVale – Sundials</title>
<link href="https://fonts.googleapis.com/css2?family=Roboto:wght@400;500;700&family=Open+Sans:wght@400;600&display=swap" rel="stylesheet">
<style>
:root{
  --red:#c0150f;
  --red-deep:#a8120d;
  --red-bar:#b5160e;
  --heading-red:#b71c1c;
  --gold:#f5b041;
  --footer-bg:#3a1a08;
  --text:#333333;
  --white:#ffffff;
  --line:#cfcfcf;
}
*{box-sizing:border-box;margin:0;padding:0}
html,body{width:736px;height:1200px;overflow:hidden;background:#fff}
body{position:relative;font-family:"Open Sans",Arial,sans-serif;color:var(--text)}
.abs{position:absolute}

/* header */
.site-header{position:absolute;left:0;top:0;width:736px;height:64px;background:#fff}
.brand{position:absolute;left:50px;top:24px;display:flex;align-items:center;gap:6px;font-family:"Roboto",sans-serif;font-weight:500;font-size:16px;color:var(--red)}
.brand-dot{width:10px;height:10px;border-radius:50%;background:var(--red)}
.language{position:absolute;left:467px;top:6px;width:74px;height:18px;border:1px solid #ddd;border-radius:2px;font-family:"Roboto",sans-serif;font-size:7px;color:#555;display:flex;align-items:center;padding-left:6px;gap:6px}
.call{position:absolute;left:565px;top:8px;font-family:"Roboto",sans-serif;font-size:7px;color:#555}
.call strong{font-size:12px;color:var(--red);font-weight:700;margin-left:2px}
.main-nav a{position:absolute;top:43px;font-family:"Roboto",sans-serif;font-size:7.4px;color:var(--red);text-decoration:none}

/* hero */
.hero{position:absolute;left:0;top:64px;width:736px;height:328px;background:linear-gradient(160deg,#1c2a33 0%,#3c4246 45%,#5a5a58 70%,#2c2e30 100%)}
.hero-title{position:absolute;left:50px;top:136px;font-family:"Roboto",sans-serif;font-weight:500;font-size:26px;color:var(--gold)}
.btn-order{position:absolute;left:51px;top:174px;width:109px;height:27px;border-radius:14px;background:var(--red);color:#fff;font-family:"Roboto",sans-serif;font-weight:500;font-size:10px;display:flex;align-items:center;justify-content:center}
.slider-dots span{position:absolute;top:305px;width:7px;height:7px;border:1px solid #fff;border-radius:50%}
.slider-dots span.active{background:var(--gold);border-color:var(--gold)}

/* options */
.options{position:absolute;left:0;top:392px;width:736px;height:310px;background:linear-gradient(135deg,#b5140f 0%,#c41a14 50%,#a9110c 100%)}
.photo{position:absolute;border:1px solid #111}
.photo-arrow{position:absolute;left:240px;top:470px}
.section-title-light{position:absolute;left:294px;top:429px;font-family:"Roboto",sans-serif;font-weight:500;font-size:16px;color:#fff}
.options-text{position:absolute;left:294px;top:464px;width:390px;font-size:8.2px;line-height:14.4px;color:#fff}
.field-label{position:absolute;font-family:"Open Sans",sans-serif;font-weight:600;font-size:8.2px;color:#fff}
.field{position:absolute;width:189px;height:22px;background:#fff;border-radius:2px}
.field.select{font-family:"Roboto",sans-serif;font-size:6.8px;color:#444;display:flex;align-items:center;justify-content:space-between;padding:0 8px}
.btn-create{position:absolute;left:498px;top:645px;width:189px;height:29px;background:#ea3a30;color:#fff;font-family:"Roboto",sans-serif;font-weight:500;font-size:10.5px;display:flex;align-items:center;justify-content:center;box-shadow:0 2px 3px rgba(0,0,0,.25)}

/* location */
.map-area{position:absolute;left:50px;top:742px;width:326px;height:215px;border:1px solid #222;background:radial-gradient(ellipse at 55% 55%,#b89b6a 0%,#6d7a52 25%,#24405c 55%,#102a48 100%)}
.section-title-red{position:absolute;left:414px;top:743px;font-family:"Roboto",sans-serif;font-weight:500;font-size:16px;color:var(--heading-red)}
.location-text{position:absolute;left:414px;top:769px;width:290px;font-size:7.6px;line-height:13.6px;color:#333}
.loc-label{position:absolute;left:416px;font-family:"Roboto",sans-serif;font-weight:500;font-size:8.5px;color:var(--heading-red)}
.loc-input{position:absolute;left:506px;width:179px;height:22px;border:1px solid var(--line);border-radius:2px;font-size:7.5px;padding-left:8px;display:flex;align-items:center;box-shadow:inset 0 1px 2px rgba(0,0,0,.1)}
.loc-note{position:absolute;left:417px;top:949px;font-family:"Roboto",sans-serif;font-size:7.6px;color:#333}

/* footer */
.site-footer{position:absolute;left:0;top:995px;width:736px;height:173px;background:var(--footer-bg)}
.footer-brand{position:absolute;left:50px;top:1036px;display:flex;align-items:center;gap:6px;font-family:"Roboto",sans-serif;font-weight:500;font-size:14px;color:var(--red)}
.footer-about{position:absolute;left:50px;top:1065px;width:205px;font-size:7.5px;line-height:13.6px;color:#fff;text-align:justify}
.social{position:absolute;top:1122px;width:8px;height:8px;border-radius:50%;background:var(--gold)}
.footer-heading{position:absolute;top:1030px;font-family:"Roboto",sans-serif;font-weight:500;font-size:9.6px;color:var(--gold)}
.contact-line{position:absolute;left:327px;font-size:7.4px;line-height:11px;color:#fff}
.contact-icon{position:absolute;left:308px}
.footer-links a{position:absolute;font-size:7.4px;color:#fff;text-decoration:none}
.bottom-bar{position:absolute;left:0;top:1168px;width:736px;height:32px;background:var(--red-bar);color:#fff;font-size:7.4px;display:flex;align-items:center;justify-content:center}
</style>
</head>
<body>

<header class="site-header">
  <div class="brand"><span class="brand-dot"></span>GnomonVale.com</div>
  <div class="language">LANGUAGE
    <svg width="7" height="5" viewBox="0 0 7 5"><path d="M0.5 0.5 L3.5 4 L6.5 0.5" fill="none" stroke="#777" stroke-width="1"/></svg>
  </div>
  <div class="call">CALL US : <strong>555-014-7320</strong></div>
  <nav class="main-nav">
    <a style="left:365px" href="#">HOME</a>
    <a style="left:416px" href="#">ABOUT</a>
    <a style="left:470px" href="#">PRODUCTS</a>
    <a style="left:538px" href="#">NEWS</a>
    <a style="left:589px" href="#">GALLERY</a>
    <a style="left:650px" href="#">CONTACT</a>
  </nav>
</header>

<section class="hero" role="img" aria-label="Close-up photograph of a metal sundial gnomon casting a shadow on its dial">
</section>
<h1 class="hero-title">LOREM IPSUM DOLOR SIT AMET</h1>
<div class="btn-order" style="top:238px">ORDER NOW</div>
<div class="slider-dots">
  <span style="left:330px;top:369px"></span>
  <span style="left:347px;top:369px"></span>
  <span class="active" style="left:364px;top:369px"></span>
  <span style="left:381px;top:369px"></span>
  <span style="left:398px;top:369px"></span>
</div>

<section class="options"></section>
<div class="photo" role="img" aria-label="Paper sundial mounted on a brick wall" style="left:52px;top:420px;width:187px;height:118px;background:linear-gradient(90deg,#3a3026 0%,#5a4a3a 25%,#a65a44 40%,#c9c9c4 60%,#a05640 100%)"></div>
<div class="photo" role="img" aria-label="Paper sundial fixed to a balcony window" style="left:52px;top:562px;width:187px;height:118px;background:linear-gradient(90deg,#1c1a16 0%,#2d2a24 28%,#c8ccd2 45%,#d9c2a0 60%,#9aa3ad 100%)"></div>
<svg class="photo-arrow" width="19" height="22" viewBox="0 0 19 22"><path d="M0 0 L19 11 L0 22 Z" fill="#111"/></svg>
<h2 class="section-title-light">SUNDIAL OPTIONS</h2>
<p class="options-text">Lorem ipsum dolor sit amet, consectetur adipiscing elit. Ut auctor lorem vitae dui fringilla, sed vulp utate massa rhoncus. Cras tincidunt semper elit vitae porta. Quisque in turpis id leo viverra cursus vel in ligula.</p>
<span class="field-label" style="left:298px;top:528px">BANNER</span>
<div class="field" style="left:298px;top:544px"></div>
<span class="field-label" style="left:498px;top:528px">TIMEZONE</span>
<div class="field select" style="left:498px;top:544px">(GMT+999) LOCAL TIME (SOLAR TIME)
  <svg width="7" height="5" viewBox="0 0 7 5"><path d="M0.5 0.5 L3.5 4 L6.5 0.5" fill="none" stroke="#444" stroke-width="1"/></svg>
</div>
<span class="field-label" style="left:298px;top:588px">TIMES</span>
<div class="field" style="left:298px;top:604px"></div>
<span class="field-label" style="left:498px;top:588px">DAYLIGHT SAVING TIME</span>
<div class="field" style="left:498px;top:604px"></div>
<div class="btn-create">CREATE SUNDIAL</div>

<div class="map-area" role="img" aria-label="Satellite world map for choosing the sundial location"></div>
<h2 class="section-title-red">SUNDIAL LOCATION</h2>
<p class="location-text">Select the location where you want to place your paper sundial, mark a line along building wall where you want to put it.<br>Write your address and press Go! (e.g. Picadilly circus, london, UK)</p>
<span class="loc-label" style="left:416px;top:835px">LONGITUDE</span>
<div class="loc-input" style="top:829px">0</div>
<span class="loc-label" style="left:416px;top:872px">LATITUDE</span>
<div class="loc-input" style="top:866px">0</div>
<span class="loc-label" style="left:416px;top:909px">WALL DECLINATION</span>
<div class="loc-input" style="top:902px">0</div>
<p class="loc-note">NOW SELECT THE FACE OF THE BUILDING</p>

<footer class="site-footer"></footer>
<div class="footer-brand"><span class="brand-dot"></span>GnomonVale</div>
<p class="footer-about">Lorem ipsum dolor sit amet, consectetur adipiscing elit. Etiam bibendum purus quis ipsum auctor malesuada. Mauris sit amet lectus libero. Sed id felis mattis laoreet.</p>
<span class="social" style="left:50px"></span>
<span class="social" style="left:73px"></span>
<span class="social" style="left:98px"></span>
<span class="social" style="left:124px"></span>
<span class="social" style="left:152px"></span>

<h3 class="footer-heading" style="left:308px">CONTACT US</h3>
<svg class="contact-icon" style="top:1066px" width="8" height="11" viewBox="0 0 8 11"><path d="M4 0 A4 4 0 0 1 8 4 C8 7 4 11 4 11 C4 11 0 7 0 4 A4 4 0 0 1 4 0 Z" fill="var(--gold)"/><circle cx="4" cy="4" r="1.5" fill="#3a1a08"/></svg>
<p class="contact-line" style="top:1065px">41 Meridian Court, Solar Lane<br>Brookfield 550142</p>
<svg class="contact-icon" style="top:1099px" width="9" height="9" viewBox="0 0 9 9"><path d="M1.5 0.5 L3.2 0.5 L4 2.6 L2.9 3.4 C3.5 4.7 4.3 5.5 5.6 6.1 L6.4 5 L8.5 5.8 L8.5 7.5 C8.5 8.1 8 8.5 7.4 8.5 C3.6 8.2 0.8 5.4 0.5 1.6 C0.5 1 0.9 0.5 1.5 0.5 Z" fill="var(--gold)"/></svg>
<p class="contact-line" style="top:1098px">+1 (555) 019 2846</p>
<svg class="contact-icon" style="top:1122px" width="10" height="8" viewBox="0 0 10 8"><rect width="10" height="8" rx="1" fill="var(--gold)"/><path d="M0.5 0.8 L5 4.5 L9.5 0.8" fill="none" stroke="#3a1a08" stroke-width="1"/></svg>
<p class="contact-line" style="top:1120px">support@gnomonvale.com</p>

<h3 class="footer-heading" style="left:502px;top:1029px">COMPANY</h3>
<nav class="footer-links">
  <a style="left:503px;top:1064px" href="#">Home</a>
  <a style="left:503px;top:1081px" href="#">Why Us?</a>
  <a style="left:503px;top:1098px" href="#">Products</a>
  <a style="left:503px;top:1116px" href="#">Testimonials</a>
  <a style="left:503px;top:1133px" href="#">Contact</a>
</nav>
<h3 class="footer-heading" style="left:624px">QUICK LINKS</h3>
<nav class="footer-links">
  <a style="left:625px;top:1064px" href="#">Faq</a>
  <a style="left:625px;top:1081px" href="#">News</a>
  <a style="left:625px;top:1098px" href="#">About us</a>
  <a style="left:625px;top:1116px" href="#">Privacy Policy</a>
  <a style="left:625px;top:1133px" href="#">Terms of Use</a>
</nav>
<div class="bottom-bar">Sundial © 2016 All Rights Reserved.</div>

</body>
</html>
```